New Business Card for Software Company

We are looking at rebranding a 10 year old company that specializes in PDF and DWF solutions for Architects and Engineers. We will attach the new company logo that we are going with so you can work with that and complimentary colors.
The sample information we would like on the business card is:
Gerald Pinfold
Vice President
4738 W. Harrowgate Lane. STE 305
PMB#417
Redmoor, NM 85374
866-392-5074 US Toll Free
123-456-3190 Cell
gpinfold@plavorix.com
The old tag line that we had on the business cars was.
Precision Document Tools Built for the Architects and Engineers Who Shape the World.
If you have an idea for a better tag line we are open to that also.
Updates
We would like to thank all of the Designers for their wonderful work. We apologize that we will not have the time to provide feedback to everyone. There is just so many innovative and professional designs that you have all created making our decision even harder.
Target Market(s)
Architects and Engineers
Industry/Entity Type
Business
Look and feel

```html
<!DOCTYPE html>
<html lang="en">
<head>
<meta charset="utf-8">
<title>Plavorix Business Card</title>
<link rel="stylesheet" href="https://fonts.googleapis.com/css2?family=Barlow:wght@400;500;800&display=swap">
<style>
  :root {
    --backdrop: #e4e2df;
    --card-white: #f1f1f0;
    --ink-grey: #55565a;
    --ink-dark: #4a4b4f;
    --brand-orange: #e8621c;
    --orange-light: #f5a81f;
    --orange-mid: #ef8a1c;
    --orange-deep: #e0621a;
    --band-orange: #e56a1c;
    --white: #ffffff;
  }
  * { margin: 0; padding: 0; box-sizing: border-box; }
  html, body {
    width: 1200px; height: 900px; overflow: hidden;
    background: var(--backdrop);
    font-family: "Barlow", Arial, sans-serif;
  }
  .canvas {
    position: relative; width: 1200px; height: 900px;
    display: flex; flex-direction: column; align-items: center; justify-content: center; gap: 60px;
  }
  .card {
    position: relative; width: 560px; height: 320px;
    box-shadow: 0 6px 18px rgba(0,0,0,0.18);
    overflow: hidden;
  }

  /* Back side */
  .card-back {
    background: linear-gradient(135deg, var(--orange-light) 0%, var(--orange-mid) 45%, var(--orange-deep) 100%);
  }
  .back-wordmark {
    position: absolute; left: 34px; top: 150px;
    font-weight: 800; font-size: 78px; line-height: 1; letter-spacing: -1px;
    color: var(--white);
  }
  .tagline-band {
    position: absolute; left: 34px; top: 236px;
    background: var(--band-orange);
    padding: 6px 14px 7px 14px;
    color: var(--white); font-size: 14px; line-height: 1.2; font-weight: 500;
  }

  /* Front side */
  .card-front { background: var(--card-white); }
  .front-wordmark {
    position: absolute; right: 30px; top: 26px;
    font-weight: 800; font-size: 58px; line-height: 1; letter-spacing: -1px;
    color: var(--ink-dark);
  }
  .brand-row {
    position: absolute; left: 30px; top: 104px;
    display: flex; align-items: center; gap: 12px;
  }
  .brand-dot { width: 58px; height: 58px; border-radius: 50%; background: var(--brand-orange); }
  .brand-name {
    font-weight: 800; font-size: 50px; line-height: 1; letter-spacing: -1px;
    color: var(--brand-orange);
  }
  .contact {
    position: absolute; left: 150px; top: 174px; right: 24px;
  }
  .person-name {
    font-size: 22px; font-weight: 500; letter-spacing: 0.5px; text-transform: uppercase;
    color: var(--brand-orange); line-height: 1.1;
  }
  .person-title { font-size: 16px; color: var(--ink-grey); line-height: 1.3; }
  .details {
    margin-top: 4px; padding-left: 12px;
    border-left: 2px solid var(--brand-orange);
    font-size: 14px; color: var(--ink-grey); line-height: 1.35;
  }
  .details .label {
    display: inline-block; width: 16px; font-weight: 800; color: var(--brand-orange);
  }
  .address { margin-left: 16px; }
</style>
</head>
<body>
  <main class="canvas">
    <section class="card card-back" aria-label="Business card back">
      <div class="back-wordmark">Plavorix</div>
      <p class="tagline-band">Precision Document Tools Built for the Architects<br>and Engineers Who Shape the World</p>
    </section>

    <section class="card card-front" aria-label="Business card front">
      <div class="front-wordmark">Plavorix</div>
      <div class="brand-row">
        <span class="brand-dot"></span>
        <span class="brand-name">Plavorix</span>
      </div>
      <div class="contact">
        <p class="person-name">Gerald Pinfold</p>
        <p class="person-title">Vice President</p>
        <div class="details">
          <p><span class="label">T</span>866-392-5074 US Toll Free</p>
          <p><span class="label">M</span>123-456-3190</p>
          <p><span class="label">E</span>gpinfold@plavorix.com</p>
          <p class="address">4738 W. Harrowgate Lane. STE 305, PMB#417<br>Redmoor, NM 85374</p>
        </div>
      </div>
    </section>
  </main>
</body>
</html>
```